design a construction company business card

Design business card around our logo. Card must have all the typical info: name, title, address, phone, email, business name, etc. Somewhere on the card I would like to see our motto "Built on integrity... Inspired by commitment." Consider adding a splash of bright orange to the card to complement the blues and silvers/grays in the logo. We are open to metallic inks, textures, etc. We would like to see options on both light and dark backgrounds. The font in the logo is Euro Technic Extended Regular.

```html
<!DOCTYPE html>
<html lang="en">
<head>
<meta charset="utf-8">
<title>Halden Contracting – Business Card</title>
<link rel="stylesheet" href="https://fonts.googleapis.com/css2?family=Fira+Sans:wght@400;600&display=swap">
<style>
  :root {
    --stage-light: #e9eaeb;
    --stage-dark: #cfd0d2;
    --blue-deep: #2a3a94;
    --blue-bright: #1c78c2;
    --brand-blue: #2452b0;
    --silver: #86878b;
    --ink: #4a4b4f;
    --card-white: #ffffff;
    --card-black: #231f20;
  }
  * { margin: 0; padding: 0; box-sizing: border-box; }
  html, body { width: 800px; height: 1200px; overflow: hidden; }
  body {
    position: relative;
    background: radial-gradient(ellipse at 50% 48%, var(--stage-light) 0%, var(--stage-dark) 75%);
    font-family: "Fira Sans", sans-serif;
  }
  .card {
    position: absolute;
    left: 148px;
    width: 504px;
    height: 288px;
    overflow: hidden;
  }
  .card--front { top: 164px; background: var(--card-white); }
  .card--back { top: 703px; background: var(--card-black); }

  .front-swoosh { position: absolute; inset: 0; }

  .holder { position: absolute; right: 26px; top: 20px; text-align: right; color: #fff; }
  .holder__name { font-size: 22px; font-weight: 600; line-height: 1.1; }
  .holder__title { font-size: 12.5px; font-weight: 400; margin-top: 1px; margin-right: 2px; }

  .brand {
    position: absolute;
    display: flex; align-items: center; gap: 8px;
    font-weight: 600; text-transform: uppercase; letter-spacing: 1px; line-height: 1.05;
  }
  .brand__mark { width: 12px; height: 12px; flex: none; }
  .brand--front { left: 32px; top: 128px; color: var(--brand-blue); font-size: 24px; }
  .brand--front .brand__mark { background: var(--brand-blue); }
  .brand--front .brand__sub { font-size: 24px; }
  .brand--back { left: 0; right: 0; top: 112px; justify-content: center; color: #fff; font-size: 26px; text-align: left; }
  .brand--back .brand__mark { background: #fff; }

  .contact {
    position: absolute; right: 26px; top: 177px;
    list-style: none; text-align: right;
    color: var(--ink); font-size: 12.2px; line-height: 18px;
  }
  .contact__item { display: flex; justify-content: flex-end; align-items: center; gap: 6px; }
  .contact__icon { width: 9px; height: 9px; flex: none; }
  .contact__item--address { margin-right: 0; }
</style>
</head>
<body>

<section class="card card--front" aria-label="Business card front">
  <svg class="front-swoosh" width="504" height="288" viewBox="0 0 504 288" aria-hidden="true">
    <defs>
      <linearGradient id="bandGradient" x1="0" y1="0" x2="1" y2="0">
        <stop offset="0" stop-color="var(--blue-deep)"/>
        <stop offset="1" stop-color="var(--blue-bright)"/>
      </linearGradient>
    </defs>
    <rect width="504" height="175" fill="url(#bandGradient)"/>
    <path d="M0,64 C120,20 330,24 504,170" fill="none" stroke="var(--silver)" stroke-width="5"/>
    <path d="M0,69 C120,27 330,32 504,178 L504,288 L0,288 Z" fill="var(--card-white)"/>
  </svg>

  <div class="holder">
    <div class="holder__name">Daniel Whitford</div>
    <div class="holder__title">Managing Member</div>
  </div>

  <div class="brand brand--front">
    <span class="brand__mark"></span>
    <span>Halden<br><span class="brand__sub">Contracting, Inc.</span></span>
  </div>

  <ul class="contact">
    <li class="contact__item">(555) 214-3870
      <svg class="contact__icon" viewBox="0 0 10 10"><path d="M2,1 L4,1 L4.6,3 L3.4,3.8 C4,5.2 4.8,6 6.2,6.6 L7,5.4 L9,6 L9,8 C9,8.6 8.4,9 7.8,9 C4,8.6 1.4,6 1,2.2 C1,1.6 1.4,1 2,1 Z" fill="var(--blue-bright)"/></svg>
    </li>
    <li class="contact__item">(555) 498-1162
      <svg class="contact__icon" viewBox="0 0 10 10"><rect x="2.5" y="0.5" width="5" height="9" rx="1" fill="none" stroke="var(--blue-bright)" stroke-width="1.2"/><rect x="4.2" y="7.6" width="1.6" height="0.9" fill="var(--blue-bright)"/></svg>
    </li>
    <li class="contact__item">daniel@haldenbuild.com
      <svg class="contact__icon" viewBox="0 0 10 10"><rect x="0.5" y="2" width="9" height="6.5" fill="var(--blue-bright)"/><path d="M0.5,2 L5,5.6 L9.5,2" fill="none" stroke="#fff" stroke-width="0.9"/></svg>
    </li>
    <li class="contact__item">www.haldenbuild.com
      <svg class="contact__icon" viewBox="0 0 10 10"><circle cx="5" cy="5" r="4.3" fill="var(--blue-bright)"/><path d="M0.7,5 H9.3 M5,0.7 V9.3 M5,0.7 C2.6,3 2.6,7 5,9.3 M5,0.7 C7.4,3 7.4,7 5,9.3" fill="none" stroke="#fff" stroke-width="0.6"/></svg>
    </li>
    <li class="contact__item contact__item--address">2250 Harbor Point Rd, Riverton, CA 95120</li>
  </ul>
</section>

<section class="card card--back" aria-label="Business card back">
  <div class="brand brand--back">
    <span class="brand__mark"></span>
    <span>Halden<br>Contracting, Inc.</span>
  </div>
</section>

</body>
</html>
```